Electric mountain bike tours nz

We are an Electric Mountain bike tour company in New Zealand. We will be offering bike rental and guided tours around the Nelson region in New Zealand. I want our website to represent both Mountain biking and New Zealand with the colours layout and features. We want tabs for the following:
-1 about us
-2 what we offer
-3 bookings/contact
Under the about us tab will be who we are as a a company. I want the ability to add videos to each of these tabs as we move foward with videos of the tracks we will be riding. I want the website to be editable so I can add and remove videos/photos myself. Also "our bikes" will be under this tab.
Under the what we offer tab will be
-1 bike rental and pricing
-2 guided tours and pricing
-3 recommended package deals.
I want to able to put the tracks under the guided tours tab and select beginner/ intermediate/advanced and have the tracks in each of the following to match the rider level. Also to be able to have a small video of the track would be great in this section.
Bookings and contact tab
(Further information for this tab to be updated soon)
Coded - Design and coding required
1 page
- Silver ferns, kiwi, mountains

```html
<!DOCTYPE html>
<html lang="en">
<head>
<meta charset="utf-8">
<title>Trailvolt – Electric Mountain Bike Tours</title>
<link href="https://fonts.googleapis.com/css2?family=Lato:ital,wght@0,400;0,700;0,900;1,400&display=swap" rel="stylesheet">
<style>
:root{
  --ink:#111;
  --text:#555;
  --muted:#9a9a9a;
  --white:#fff;
  --band:#c3c3c3;
  --footer:#0b0b0b;
  --bar:#3b3b3b;
  --field:#c8c8c8;
  --hero-top:#5d6f86;
  --hero-mid:#3f5a44;
  --hero-low:#4f5a2c;
  --offer-top:#2e3a44;
  --offer-low:#3b3128;
}
*{box-sizing:border-box;margin:0;padding:0}
html,body{width:1200px;height:3346px;overflow:hidden;background:var(--white)}
body{position:relative;font-family:"Lato",Arial,sans-serif;color:var(--ink)}
.abs{position:absolute}
.btn{position:absolute;display:flex;align-items:center;justify-content:center;font-weight:700;font-size:15px;border:2px solid var(--ink);color:var(--ink);background:var(--white)}
.btn-light{border-color:var(--white);color:var(--white);background:transparent}

/* header */
.site-header{position:absolute;left:0;top:0;width:1200px;height:138px;background:var(--white)}
.brand{position:absolute;left:90px;top:28px;display:flex;align-items:center;gap:10px;font-weight:900;font-size:24px;color:var(--ink)}
.brand-dot{width:22px;height:22px;border-radius:50%;background:var(--ink)}
.callbar{position:absolute;right:70px;top:37px;display:flex;align-items:center;gap:8px;font-size:17px;font-weight:700}
.social{display:flex;gap:4px}
.social i{display:block;width:16px;height:16px;border-radius:50%;background:var(--ink)}
.nav{position:absolute;right:70px;top:86px;display:flex;gap:52px;font-size:14px;font-weight:700}
.nav .current{color:var(--muted);font-weight:400}

/* hero */
.hero{position:absolute;left:0;top:138px;width:1200px;height:587px;
  background:linear-gradient(180deg,var(--hero-top) 0%,#7c8a94 25%,var(--hero-mid) 55%,var(--hero-low) 100%)}
.hero h1{position:absolute;left:0;width:1200px;top:228px;text-align:center;color:var(--white);font-size:68px;font-weight:900;line-height:1}
.hero p{position:absolute;left:0;width:1200px;top:325px;text-align:center;color:var(--white);font-size:18px;line-height:24px}
.arrow{position:absolute}

/* about */
.about h2,.offer h2{font-size:30px;font-weight:700}
.about h2 span,.offer h2 span{color:var(--muted);font-weight:400}
.about-text{position:absolute;left:90px;top:846px;width:557px;font-size:14.5px;line-height:23px;color:var(--text);text-align:justify}
.video{position:absolute;left:716px;top:854px;width:397px;height:237px;background:linear-gradient(160deg,#dfe9f2,#8fa9c0 55%,#2b3440)}
.video-bar{position:absolute;left:0;bottom:0;width:100%;height:28px;background:#111}

/* offer */
.offer{position:absolute;left:0;top:1193px;width:1200px;height:725px;background:linear-gradient(180deg,var(--offer-top),#262b2d 55%,var(--offer-low))}
.offer h2{position:absolute;top:60px;width:1200px;text-align:center;color:var(--white)}
.offer h2 span{color:#b5b5b5}
.offer-intro{position:absolute;top:118px;width:1200px;text-align:center;color:var(--white);font-size:14px;line-height:25px}
.card{position:absolute;top:225px;width:279px}
.card-photo{width:279px;height:239px;border:4px solid var(--white)}
.card h3{margin-top:30px;font-size:16px;font-weight:700;color:var(--white)}
.card p{margin-top:8px;font-size:12.5px;line-height:16.5px;color:#e6e6e6}
.card .btn{top:393px;left:31px;width:111px;height:40px;background:transparent;border-color:var(--white);color:var(--white)}

/* blog */
.section-title{position:absolute;width:1200px;text-align:center;font-size:28px;font-weight:700}
.blog-tile{position:absolute;top:2034px;width:300px;height:272px}
.blog-tile h4{position:absolute;top:110px;width:100%;text-align:center;color:var(--white);font-size:19px;font-weight:700}
.blog-tile time{position:absolute;top:138px;width:100%;text-align:center;color:var(--white);font-size:14px}
.blog-go{position:absolute;right:0;bottom:0;width:30px;height:30px;background:#000}

/* testimonials */
.band{position:absolute;left:0;top:2634px;width:1200px;height:263px;background:var(--band)}
.avatar{position:absolute;border:3px solid var(--white)}
.quote{position:absolute;top:2718px;left:220px;width:760px;text-align:center;font-style:italic;font-size:12.5px;line-height:16px;color:var(--white)}
.author{position:absolute;top:2800px;width:1200px;text-align:center;font-size:14px;font-weight:700;color:var(--white)}
.dots{position:absolute;top:2838px;left:568px;display:flex;gap:8px}
.dots i{width:10px;height:10px;border-radius:50%;background:#ddd}
.dots i.on{background:transparent;border:1.5px solid #333}

/* footer */
.site-footer{position:absolute;left:0;top:2897px;width:1200px;height:395px;background:linear-gradient(160deg,#1a1a1a,var(--footer) 45%)}
.site-footer h3{position:absolute;color:var(--white);font-size:19px;font-weight:700}
.field{position:absolute;border:1.5px solid #bbb;color:var(--white);font-size:11.5px;padding:8px 6px}
.btn-grey{position:absolute;background:var(--field);display:flex;align-items:center;justify-content:center;font-size:14px;color:var(--ink)}
.legal{position:absolute;left:0;top:3292px;width:1200px;height:54px;background:var(--bar);color:#ccc;font-size:13px;display:flex;align-items:center;justify-content:center}
</style>
</head>
<body>

<header class="site-header">
  <div class="brand"><span class="brand-dot"></span>Trailvolt</div>
  <div class="callbar">
    <svg width="18" height="18" viewBox="0 0 24 24"><circle cx="12" cy="12" r="12" fill="#111"/><path d="M8 6l2 0 1 3-1.5 1a7 7 0 0 0 4 4l1-1.5 3 1v2a1.5 1.5 0 0 1-1.5 1.5A10 10 0 0 1 6.5 7.5 1.5 1.5 0 0 1 8 6z" fill="#fff"/></svg>
    <span>Call us Now : (021) 555 0142</span>
    <span class="social"><i></i><i></i><i></i><i></i></span>
  </div>
  <nav class="nav"><span class="current">About us</span><span>What we offer</span><span>Bookings/Contact</span></nav>
</header>

<section class="hero" role="img" aria-label="Two riders on mountain bikes on a grassy alpine trail below snowy peaks">
  <svg class="arrow" style="left:58px;top:280px" width="32" height="64" viewBox="0 0 32 64"><path d="M28 4L6 32l22 28" stroke="#fff" stroke-opacity=".7" stroke-width="5" fill="none"/></svg>
  <svg class="arrow" style="left:1110px;top:280px" width="32" height="64" viewBox="0 0 32 64"><path d="M4 4l22 28L4 60" stroke="#fff" stroke-opacity=".7" stroke-width="5" fill="none"/></svg>
  <h1>Trailvolt</h1>
  <p>We are an Electric Mountain bike tour company in New Zealand.<br>We will be offering bike rental and guided tours around the Nelson region in New Zealand.</p>
  <a class="btn btn-light" style="left:537px;top:404px;width:125px;height:40px;font-weight:400;font-size:13px">READ MORE</a>
</section>

<section class="about">
  <h2 class="abs" style="left:90px;top:790px">About <span>Us</span></h2>
  <p class="about-text">Lorem ipsum dolor sit amet, consectetuer adipiscing elit. Aenean commodo ligula eget dolor. Aenean massa. Cum sociis natoque penatibus et magnis dis parturient montes, nascetur ridiculus mus. Donec quam felis, ultricies nec, pellentesque eu, pretium quis, sem. Nulla consequat massa quis enim. Donec pede justo, fringilla vel, aliquet nec, vulputate eget, arcu. In enim justo, rhoncus ut, imperdiet a, venenatis vitae, justo. Nullam dictum felis eu pede mollis pretium. Integer tincidunt. Cras dapibus. Vivamus elementum semper nisi.</p>
  <a class="btn" style="left:91px;top:1053px;width:143px;height:38px">Read More</a>
  <div class="video" role="img" aria-label="Trail video of a rider on a snowy forest track">
    <svg class="abs" style="left:176px;top:86px" width="44" height="44" viewBox="0 0 44 44"><circle cx="22" cy="22" r="21" fill="#fff"/><path d="M17 13l13 9-13 9z" fill="#222"/></svg>
    <div class="video-bar">
      <svg class="abs" style="left:8px;top:8px" width="30" height="12" viewBox="0 0 30 12"><path d="M0 0l9 6-9 6z" fill="#fff"/><rect x="18" y="0" width="3" height="12" fill="#fff"/><rect x="24" y="0" width="3" height="12" fill="#fff"/></svg>
      <div class="abs" style="left:50px;top:12px;width:330px;height:4px;background:#666"></div>
      <div class="abs" style="left:50px;top:12px;width:120px;height:4px;background:#d11"></div>
    </div>
  </div>
</section>

<section class="offer">
  <h2>What we <span>Offer</span></h2>
  <p class="offer-intro">Lorem ipsum dolor sit amet, consectetuer adipiscing elit. Aenean commodo ligula eget dolor. Aenean massa.<br>Cum sociis natoque penatibus et magnis dis parturient montes, nascetur ridiculus mus.</p>
  <svg class="arrow" style="left:56px;top:320px" width="32" height="64" viewBox="0 0 32 64"><path d="M28 4L6 32l22 28" stroke="#fff" stroke-opacity=".7" stroke-width="5" fill="none"/></svg>
  <svg class="arrow" style="left:1112px;top:320px" width="32" height="64" viewBox="0 0 32 64"><path d="M4 4l22 28L4 60" stroke="#fff" stroke-opacity=".7" stroke-width="5" fill="none"/></svg>

  <article class="card" style="left:147px">
    <div class="card-photo" role="img" aria-label="Red mountain bike on a hilltop above a coastal valley" style="background:linear-gradient(180deg,#7aa6d6,#c9d4de 40%,#3c5b7a 60%,#4a5a3a)"></div>
    <h3>Bike rental &amp; pricing</h3>
    <p>Lorem ipsum dolor sit amet, consectetuer adipiscing elit. Aenean commodo ligula eget dolor. Aenean massa. Cum sociis natoque penatibus et magnis dis parturient montes, nascetur ridiculus mus.</p>
    <a class="btn">Read More</a>
  </article>
  <article class="card" style="left:462px">
    <div class="card-photo" role="img" aria-label="Two riders standing with their electric mountain bikes" style="background:linear-gradient(180deg,#a8b8c4,#8a8c86 50%,#4a4846)"></div>
    <h3>Guided tours &amp; pricing</h3>
    <p>Lorem ipsum dolor sit amet, consectetuer adipiscing elit. Aenean commodo ligula eget dolor. Aenean massa. Cum sociis natoque penatibus et magnis dis parturient montes, nascetur ridiculus mus.</p>
    <a class="btn">Read More</a>
  </article>
  <article class="card" style="left:776px">
    <div class="card-photo" role="img" aria-label="Group of riders on a green forest trail" style="background:linear-gradient(180deg,#9cc46a,#5f8a3a 50%,#8a7a55)"></div>
    <h3>Recommended package deals</h3>
    <p>Lorem ipsum dolor sit amet, consectetuer adipiscing elit. Aenean commodo ligula eget dolor. Aenean massa. Cum sociis natoque penatibus et magnis dis parturient montes, nascetur ridiculus mus.</p>
    <a class="btn">Read More</a>
  </article>
</section>

<section class="blog">
  <h2 class="section-title" style="top:1956px">Latest Blog</h2>
  <article class="blog-tile" style="left:0;background:linear-gradient(160deg,#8a7a4a,#4e4630)" role="img" aria-label="Rider in autumn woodland">
    <h4>Lorem ipsum dolor sit amet</h4><time>October 25, 2017</time>
    <svg class="blog-go" viewBox="0 0 30 30"><rect width="30" height="30" fill="#000"/><path d="M9 9l6 6-6 6M15 9l6 6-6 6" stroke="#fff" stroke-width="2" fill="none"/></svg>
  </article>
  <article class="blog-tile" style="left:300px;background:linear-gradient(160deg,#b89868,#6d5a3a)" role="img" aria-label="Rider beside rocky outcrop">
    <h4>Lorem ipsum dolor sit amet</h4><time>October 25, 2017</time>
    <svg class="blog-go" viewBox="0 0 30 30"><rect width="30" height="30" fill="#000"/><path d="M9 9l6 6-6 6M15 9l6 6-6 6" stroke="#fff" stroke-width="2" fill="none"/></svg>
  </article>
  <article class="blog-tile" style="left:600px;background:linear-gradient(160deg,#6f8a5a,#2f4530)" role="img" aria-label="Riders descending a grassy slope">
    <h4>Lorem ipsum dolor sit amet</h4><time>November 10, 2017</time>
    <svg class="blog-go" viewBox="0 0 30 30"><rect width="30" height="30" fill="#000"/><path d="M9 9l6 6-6 6M15 9l6 6-6 6" stroke="#fff" stroke-width="2" fill="none"/></svg>
  </article>
  <article class="blog-tile" style="left:900px;background:linear-gradient(160deg,#8fa6c0,#8a4e36 60%,#5a3020)" role="img" aria-label="Rider on red rock ridge">
    <h4>Lorem ipsum dolor sit amet</h4><time>December 25, 2017</time>
    <svg class="blog-go" viewBox="0 0 30 30"><rect width="30" height="30" fill="#000"/><path d="M9 9l6 6-6 6M15 9l6 6-6 6" stroke="#fff" stroke-width="2" fill="none"/></svg>
  </article>
  <a class="btn" style="left:529px;top:2362px;width:140px;height:38px">Read More</a>
</section>

<section class="testimonials">
  <h2 class="section-title" style="top:2484px">Testimonials</h2>
  <div class="band"></div>
  <div class="avatar" role="img" aria-label="Customer portrait" style="left:406px;top:2585px;width:87px;height:89px;background:linear-gradient(#e8c9a0,#b48a60)"></div>
  <div class="avatar" role="img" aria-label="Customer portrait" style="left:549px;top:2571px;width:116px;height:116px;background:linear-gradient(#d8d0c8,#9c8878)"></div>
  <div class="avatar" role="img" aria-label="Customer portrait" style="left:718px;top:2585px;width:89px;height:89px;background:linear-gradient(#9aa4ae,#5a4030)"></div>
  <p class="quote">Lorem ipsum dolor sit amet, consectetuer adipiscing elit. Aenean commodo ligula eget dolor. Aenean massa. Cum sociis natoque penatibus et magnis dis parturient montes, nascetur ridiculus mus. Donec quam felis, ultricies nec, pellentesque eu, pretium quis, sem. Nulla consequat massa quis enim. Donec pede justo, fringilla vel, aliquet nec, vulputate eget, arcu.</p>
  <p class="author">JAMIE ROWE</p>
  <div class="dots"><i class="on"></i><i></i><i></i><i></i></div>
</section>

<footer class="site-footer">
  <h3 style="left:129px;top:60px">Booking</h3>
  <div class="field" style="left:129px;top:107px;width:214px;height:34px">First Name:</div>
  <div class="field" style="left:352px;top:107px;width:212px;height:34px">LastName :</div>
  <div class="field" style="left:129px;top:149px;width:214px;height:34px">Phone No :</div>
  <div class="field" style="left:352px;top:149px;width:212px;height:34px">Email Address :</div>
  <div class="field" style="left:129px;top:194px;width:435px;height:87px">Message :</div>
  <div class="btn-grey" style="left:129px;top:314px;width:119px;height:27px">Submit</div>

  <h3 style="left:687px;top:70px">Newsletter</h3>
  <p class="abs" style="left:687px;top:108px;font-size:12px;color:#fff">Spam free, tasty news in your inbox Once a week..</p>
  <div class="field" style="left:687px;top:145px;width:390px;height:33px">Enter e-mail*</div>
  <div class="btn-grey" style="left:687px;top:196px;width:120px;height:29px">Subscribe</div>

  <h3 style="left:687px;top:262px">Follow us on</h3>
  <div class="abs" style="left:687px;top:296px;width:28px;height:2px;background:#fff"></div>
  <div class="abs" style="left:687px;top:322px;display:flex;gap:5px"><i style="width:18px;height:18px;border-radius:50%;background:#fff;display:block"></i><i style="width:18px;height:18px;border-radius:50%;background:#fff;display:block"></i><i style="width:18px;height:18px;border-radius:50%;background:#fff;display:block"></i><i style="width:18px;height:18px;border-radius:50%;background:#fff;display:block"></i></div>

  <h3 style="left:883px;top:262px">Call us on</h3>
  <div class="abs" style="left:883px;top:296px;width:28px;height:2px;background:#fff"></div>
  <p class="abs" style="left:883px;top:316px;font-size:25px;color:#fff">021-555-0142</p>
</footer>

<div class="legal">© 2017 trailvolt &nbsp;|&nbsp; Privacy Policy &nbsp;|&nbsp; User Agreement</div>

</body>
</html>
```